Web Design job - Condo Debts Collection Business needs a Web Design

I need a site for a client, who works with condo debts collection, and ensure all revenues provided by condo fees will be always available to the building manager of condo on a specific date, regardless of defaults.
I have the visual identity (logo, slogan and colors) of the company, and some requirements on layout (kind of slider, menu options, phone number on a noble position, etc) - maybe I can do a sketch, but I like the idea of give some freedom to designer.

*** PLEASE, we have no interest in templates. We want something new***

Target Market(s)

I have two targets for this design: - Condominium's building manager. This target is looking for a solution to overdue debts on it's condo. - Residents on condominiums. This target wants to live in a better place, where their neighbors pay their condominium fees on time.

Number of Pages Required

1 page

Requirements
Must have
• - Slider with title, some short text related, a nice image (I prefer happy and/or peaceful family, people doing business, happy friends, and so on).
• - I have a special attention to menu. I'm looking for one I can have a nice effect, more elegant, charming, kind of innovative.
• - Phone number on the top (or clearly visible).
• - Member log in area or icon on the top (or clearly visible).
• - News/articles area.
• - Modern fonts, with good quality, sans-serif on areas where reading is more intensive (prefer Google web-fonts).
• - Colors specified on attached files.
Nice to have
• - Clear background color, cause it's better to read larger texts (like articles). Dark backgrounds makes reading difficult.
• - A site with effects (like shadows, lines, curves, gradients, lights) is usually pretty.
• - I pay attention on beautiful footers.
Should not have
• - Images with a lot of money (I don't sell richness, I sell tranquility, peace, harmony, safety).
• - Poor menu.

```html
<!DOCTYPE html>
<html lang="en">
<head>
<meta charset="utf-8">
<title>Vantori – Condo Debts Collection</title>
<link rel="stylesheet" href="https://fonts.googleapis.com/css2?family=Montserrat:wght@500;600;700&family=Open+Sans:wght@400;600;700&display=swap">
<style>
:root{
  --gold:#e3b021;
  --gold-deep:#d39a14;
  --gold-light:#f0c93a;
  --ink:#1f1f1f;
  --text:#555;
  --muted:#888;
  --gray-bg:#f1f1f1;
  --white:#fff;
  --head:"Montserrat",sans-serif;
  --body:"Open Sans",sans-serif;
}
*{box-sizing:border-box;margin:0;padding:0}
html,body{width:1200px;height:3636px;overflow:hidden}
body{position:relative;background:var(--white);font-family:var(--body);color:var(--text)}
.abs{position:absolute}

/* Header */
.site-header{position:absolute;left:0;top:0;width:1200px;height:145px;background:var(--white);z-index:3}
.brand{position:absolute;left:100px;top:58px;display:flex;align-items:center;gap:12px}
.brand-mark{width:40px;height:40px;background:var(--gold)}
.brand-name{font-family:var(--head);font-weight:700;font-size:40px;color:var(--ink);letter-spacing:-1px}
.call{position:absolute;left:690px;top:64px;font-family:var(--head);font-weight:600;font-size:17px;color:var(--ink);display:flex;align-items:center;gap:8px}
.member-btn{position:absolute;left:937px;top:52px;width:163px;height:44px;border-radius:22px;background:var(--gold);color:#fff;font-family:var(--head);font-weight:700;font-size:13px;display:flex;align-items:center;justify-content:center;gap:6px}
.main-nav{position:absolute;left:500px;top:108px;display:flex;gap:30px;font-family:var(--head);font-weight:600;font-size:14px;color:var(--ink)}
.main-nav .active{color:var(--gold)}

/* Hero */
.hero-band{left:0;top:145px;width:1200px;height:640px;background:var(--gold);clip-path:polygon(0 0,100% 0,100% 75%,50% 100%,0 75%)}
.hero-photo{left:0;top:145px;width:1200px;height:620px;background:linear-gradient(160deg,#8fa1ad 0%,#c48a5a 35%,#8a4a32 65%,#5c4a44 100%);clip-path:polygon(0 0,100% 0,100% 76%,50% 100%,0 76%)}
.hero-shade{left:0;top:145px;width:1200px;height:620px;background:rgba(0,0,0,.25);clip-path:polygon(0 0,100% 0,100% 76%,50% 100%,0 76%)}
.hero-title{left:0;top:300px;width:1200px;text-align:center;font-family:var(--head);font-weight:700;font-size:68px;color:#fff;text-shadow:0 2px 6px rgba(0,0,0,.35)}
.hero-text{left:180px;top:392px;width:840px;text-align:center;font-size:21px;font-weight:600;line-height:34px;color:#fff}
.dots{left:568px;top:675px;display:flex;gap:5px}
.dots span{width:12px;height:12px;border-radius:50%;border:2px solid #fff}
.dots span.on{background:#fff}

/* Section titles */
.section-title{left:0;width:1200px;text-align:center;font-family:var(--head);font-weight:700;font-size:37px;color:var(--ink)}
.lead{font-size:13px;line-height:26px;color:var(--text);text-align:center}

/* Features */
.feature{width:300px;text-align:center}
.diamond{width:120px;height:120px;border:1.5px solid var(--gold);transform:rotate(45deg);margin:27px auto 0}
.diamond-icon{position:absolute;left:110px;top:45px;width:80px;height:80px}
.feature h3{margin-top:90px;font-family:var(--head);font-weight:600;font-size:19px;color:var(--ink)}
.feature p{margin-top:14px;font-size:13px;line-height:25px}

/* Why choose */
.why-band{left:0;top:1445px;width:1200px;height:720px;background:var(--gold);clip-path:polygon(0 0,50% 14%,100% 0,100% 100%,50% 87%,0 100%)}
.why-bg{left:0;top:1470px;width:1200px;height:670px;background:var(--gray-bg);clip-path:polygon(0 0,50% 11%,100% 0,100% 100%,50% 86%,0 100%)}
.why-title{left:100px;top:1590px;font-family:var(--head);font-weight:700;font-size:36px;color:var(--ink)}
.why-lead{left:100px;top:1662px;width:460px;font-size:13px;line-height:26px}
.why-item{left:100px;width:480px;display:flex;gap:22px}
.why-item svg{flex:0 0 50px}
.why-item h4{font-family:var(--head);font-weight:600;font-size:18px;color:var(--ink)}
.why-item p{font-size:13px;margin-top:12px}
.video{left:615px;top:1648px;width:487px;height:327px;background:#fff;padding:6px;box-shadow:0 2px 6px rgba(0,0,0,.15)}
.video-still{width:100%;height:100%;background:linear-gradient(135deg,#e9e6e3 0%,#b9aca2 45%,#6e6a68 100%)}
.play{left:852px;top:1782px;width:60px;height:60px;border-radius:50%;background:#1a1a1a}

/* News */
.news-card{top:2290px;width:322px}
.news-img{height:210px}
.news-card h3{margin-top:36px;font-family:var(--head);font-weight:600;font-size:18px;color:var(--ink)}
.meta{margin-top:16px;font-size:12px;color:var(--muted);display:flex;gap:14px;align-items:center}
.meta i{display:inline-block;width:10px;height:10px;background:var(--gold);border-radius:2px;margin-right:5px}
.news-card p{margin-top:12px;font-size:12px;line-height:22px}
.read-more{display:block;margin-top:18px;font-family:var(--head);font-weight:700;font-size:12px;color:var(--gold)}

/* Testimonials */
.testi-bg{left:0;top:2742px;width:1200px;height:640px;background:linear-gradient(180deg,var(--gold-deep) 0%,var(--gold) 55%,var(--gold-light) 100%);clip-path:polygon(0 0,50% 10%,100% 0,100% 100%,50% 92%,0 100%)}
.testi-title{left:0;top:2888px;width:1200px;text-align:center;font-family:var(--head);font-weight:700;font-size:37px;color:#fff}
.testi-card{top:3012px;width:308px;height:200px;border:2px solid rgba(255,255,255,.85);border-radius:4px;text-align:center;color:#fff;padding:72px 30px 0}
.testi-card p{font-size:12px;font-style:italic;line-height:20px}
.testi-card h5{margin-top:14px;font-family:var(--head);font-weight:600;font-size:17px}
.avatar{top:2968px;width:86px;height:86px;border-radius:50%;border:4px solid #fff;background:linear-gradient(160deg,#d9cbbf,#8e7f74)}
.arrow{top:3096px;width:36px;height:36px;border-radius:50%;background:rgba(255,255,255,.35);display:flex;align-items:center;justify-content:center}

/* Footer */
.socials{left:487px;top:3380px;display:flex;gap:10px}
.socials span{width:52px;height:52px;border-radius:50%;border:1.5px solid #bbb}
.foot-line{left:0;width:1200px;text-align:center;font-size:14px;color:var(--text)}
.foot-line .sep{margin:0 12px;color:#999}
.copy{left:0;top:3565px;width:1200px;text-align:center;font-size:14px;color:var(--muted)}
</style>
</head>
<body>

<header class="site-header">
  <div class="brand"><span class="brand-mark"></span><span class="brand-name">vantori</span></div>
  <div class="call">
    <svg width="16" height="16" viewBox="0 0 24 24"><path fill="#e3b021" d="M6.6 10.8a15 15 0 0 0 6.6 6.6l2.2-2.2c.3-.3.7-.4 1-.2 1.1.4 2.3.6 3.6.6.6 0 1 .4 1 1V20c0 .6-.4 1-1 1A17 17 0 0 1 3 4c0-.6.4-1 1-1h3.5c.6 0 1 .4 1 1 0 1.3.2 2.5.6 3.6.1.3 0 .7-.2 1z"/></svg>
    CALL US : (55) 3100.4820
  </div>
  <div class="member-btn">
    <svg width="12" height="12" viewBox="0 0 24 24"><circle cx="12" cy="7" r="5" fill="#fff"/><path d="M2 23c0-6 4-9 10-9s10 3 10 9z" fill="#fff"/></svg>
    MEMBER LOG IN
  </div>
  <nav class="main-nav">
    <span class="active">HOME</span><span>ABOUT US</span><span>SERVICES</span><span>BLOG</span><span>RESOURCES</span><span>CONTACT</span>
    <svg width="15" height="15" viewBox="0 0 24 24"><circle cx="10" cy="10" r="7" stroke="#1f1f1f" stroke-width="3" fill="none"/><path d="M15 15l7 7" stroke="#1f1f1f" stroke-width="3"/></svg>
  </nav>
</header>

<section class="hero">
  <div class="abs hero-band"></div>
  <div class="abs hero-photo" role="img" aria-label="Group of happy friends celebrating outdoors by the sea at sunset"></div>
  <div class="abs hero-shade"></div>
  <h1 class="abs hero-title">CONDO DEBTS COLLECTION</h1>
  <p class="abs hero-text">Ensure all revenues provided by condo fees will be always available to the building manager of condo on a specific date, regardless of defaults.</p>
  <div class="abs dots"><span class="on"></span><span></span><span></span><span></span></div>
</section>

<section class="welcome">
  <h2 class="abs section-title" style="top:855px">WELCOME TO VANTORI</h2>
  <p class="abs lead" style="left:190px;top:925px;width:820px">Nam libero tempore, cum soluta nobis est eligendi optio cumque nihil impedit quo minus id quod maxime placeat facere possi mus, omnis voluptas assumenda est, omnis dolor repelle ibus autem quibusdam et aut officiis debitis au</p>

  <div class="abs feature" style="left:100px;top:1045px">
    <div class="diamond"></div>
    <svg class="diamond-icon" viewBox="0 0 80 80"><path d="M20 32h36l-8-8M60 48H24l8 8" stroke="#e3b021" stroke-width="6" fill="none" stroke-linejoin="round"/></svg>
    <h3>SEAMLESS COLLECTIONS</h3>
    <p>At vero eos et accusamus et iusto odio dign issimos ducimus qui blanditiis praesentium volu ptatum deleniti atque corrupti quos</p>
  </div>
  <div class="abs feature" style="left:450px;top:1045px">
    <div class="diamond"></div>
    <svg class="diamond-icon" viewBox="0 0 80 80"><rect x="18" y="24" width="36" height="36" rx="3" stroke="#e3b021" stroke-width="5" fill="none"/><path d="M34 46l22-22 5 5-22 22-7 2z" fill="#e3b021"/></svg>
    <h3>CREDIT REPORTING</h3>
    <p>At vero eos et accusamus et iusto odio dign issimos ducimus qui blanditiis praesentium volu ptatum deleniti atque corrupti quos</p>
  </div>
  <div class="abs feature" style="left:800px;top:1045px">
    <div class="diamond"></div>
    <svg class="diamond-icon" viewBox="0 0 80 80"><rect x="12" y="26" width="56" height="30" fill="#e3b021"/><circle cx="40" cy="41" r="9" fill="#fff"/><rect x="38" y="36" width="4" height="10" fill="#e3b021"/></svg>
    <h3>NO COMMISSIONS EVER</h3>
    <p>At vero eos et accusamus et iusto odio dign issimos ducimus qui blanditiis praesentium volu ptatum deleniti atque corrupti quos</p>
  </div>
</section>

<section class="why">
  <div class="abs why-band"></div>
  <div class="abs why-bg"></div>
  <h2 class="why-title abs">WHY CHOOSE VANTORI?</h2>
  <p class="abs why-lead">Nam libero tempore, cum soluta nobis est eligendi optio cumque nihil impedit quo minus id quod maxime plac.</p>

  <div class="abs why-item" style="top:1745px">
    <svg width="50" height="50" viewBox="0 0 50 50"><polygon points="25,2 30,9 39,7 40,16 48,20 43,28 47,36 38,39 36,48 27,44 20,50 16,42 7,41 9,32 2,25 9,18 7,9 16,8 20,1" fill="#e3b021"/></svg>
    <div><h4>Collection Experience</h4><p>Temporibus autem quibusdam et aut officiis debitis aut</p></div>
  </div>
  <div class="abs why-item" style="top:1838px">
    <svg width="50" height="50" viewBox="0 0 50 50"><rect x="4" y="22" width="9" height="24" fill="#e3b021"/><path d="M16 22l9-16c4 0 5 3 4 7l-2 7h13c3 0 5 3 4 6l-4 16c-1 3-3 4-6 4H16z" fill="#e3b021"/></svg>
    <div><h4>Effective Best Practices Collections</h4><p>Temporibus autem quibusdam et aut officiis debitis aut</p></div>
  </div>
  <div class="abs why-item" style="top:1932px">
    <svg width="50" height="50" viewBox="0 0 50 50"><path d="M25 3L48 46H2z" fill="#e3b021"/><rect x="22.5" y="17" width="5" height="16" fill="#fff"/><rect x="22.5" y="37" width="5" height="5" fill="#fff"/></svg>
    <div><h4>No Risk</h4><p>Temporibus autem quibusdam et aut officiis debitis aut</p></div>
  </div>

  <div class="abs video"><div class="video-still" role="img" aria-label="Video still of hands using a calculator over paperwork"></div></div>
  <div class="abs play"><svg width="60" height="60" viewBox="0 0 60 60"><path d="M24 18l18 12-18 12z" fill="#fff"/></svg></div>
</section>

<section class="news">
  <h2 class="abs section-title" style="top:2183px">LATEST NEWS</h2>

  <article class="abs news-card" style="left:100px">
    <div class="news-img" role="img" aria-label="Hand typing on a card payment terminal" style="background:linear-gradient(135deg,#9a9490,#4a4544)"></div>
    <h3>Finibus Bonorum et Malorum</h3>
    <div class="meta"><span><i></i>25/09/2017</span><span><i></i>Mark</span></div>
    <p>Nemo enim ipsam voluptatem quia volupta asperna tur aut odit aut fugit, sed quia conseq</p>
    <span class="read-more">READ MORE</span>
  </article>
  <article class="abs news-card" style="left:439px">
    <div class="news-img" role="img" aria-label="Business people reviewing charts on a desk" style="background:linear-gradient(135deg,#2c4a6e,#c9d3dc 60%,#8ba0b5)"></div>
    <h3>Finibus Bonorum et Malorum</h3>
    <div class="meta"><span><i></i>25/09/2017</span><span><i></i>Mark</span></div>
    <p>Nemo enim ipsam voluptatem quia volupta asperna tur aut odit aut fugit, sed quia conseq</p>
    <span class="read-more">READ MORE</span>
  </article>
  <article class="abs news-card" style="left:778px">
    <div class="news-img" role="img" aria-label="Person using a calculator and writing in a notebook" style="background:linear-gradient(135deg,#e7a064,#c1784a 50%,#7b5a4a)"></div>
    <h3>Finibus Bonorum et Malorum</h3>
    <div class="meta"><span><i></i>25/09/2017</span><span><i></i>Mark</span></div>
    <p>Nemo enim ipsam voluptatem quia volupta asperna tur aut odit aut fugit, sed quia conseq</p>
    <span class="read-more">READ MORE</span>
  </article>
</section>

<section class="testimonials">
  <div class="abs testi-bg"></div>
  <h2 class="abs testi-title">TESTIMONIALS</h2>

  <div class="abs arrow" style="left:30px"><svg width="14" height="14" viewBox="0 0 14 14"><path d="M9 2L4 7l5 5" stroke="#fff" stroke-width="2" fill="none"/></svg></div>
  <div class="abs arrow" style="left:1134px"><svg width="14" height="14" viewBox="0 0 14 14"><path d="M5 2l5 5-5 5" stroke="#fff" stroke-width="2" fill="none"/></svg></div>

  <div class="abs testi-card" style="left:100px"><p>Nam libero tempore, cum soluta nobis est eligendi optio cumque nihil impedit quo minus id quod maxime placea</p><h5>Clara Benton</h5></div>
  <div class="abs avatar" style="left:211px" role="img" aria-label="Portrait of Clara Benton"></div>

  <div class="abs testi-card" style="left:447px"><p>Nam libero tempore, cum soluta nobis est eligendi optio cumque nihil impedit quo minus id quod maxime placea</p><h5>Nora Whitfield</h5></div>
  <div class="abs avatar" style="left:558px" role="img" aria-label="Portrait of Nora Whitfield"></div>

  <div class="abs testi-card" style="left:794px"><p>Nam libero tempore, cum soluta nobis est eligendi optio cumque nihil impedit quo minus id quod maxime placea</p><h5>Daniel Rourke</h5></div>
  <div class="abs avatar" style="left:905px" role="img" aria-label="Portrait of Daniel Rourke"></div>
</section>

<footer class="site-footer">
  <div class="abs socials"><span></span><span></span><span></span><span></span></div>
  <p class="abs foot-line" style="top:3460px">
    <svg width="12" height="14" viewBox="0 0 12 16"><path d="M6 0a6 6 0 0 0-6 6c0 5 6 10 6 10s6-5 6-10a6 6 0 0 0-6-6z" fill="#e3b021"/><circle cx="6" cy="6" r="2" fill="#fff"/></svg>
    Av. Horizonte Azul, 2.400, Sala 310, Ed. Solar Center, CEP: 40.220-310, Centro, Porto Claro-BA <span class="sep">|</span>
  </p>
  <p class="abs foot-line" style="top:3490px">
    <svg width="13" height="13" viewBox="0 0 24 24"><path fill="#e3b021" d="M6.6 10.8a15 15 0 0 0 6.6 6.6l2.2-2.2c.3-.3.7-.4 1-.2 1.1.4 2.3.6 3.6.6.6 0 1 .4 1 1V20c0 .6-.4 1-1 1A17 17 0 0 1 3 4c0-.6.4-1 1-1h3.5c.6 0 1 .4 1 1 0 1.3.2 2.5.6 3.6.1.3 0 .7-.2 1z"/></svg>
    (55) 3100.4820 <span class="sep">|</span>
    <svg width="14" height="11" viewBox="0 0 14 11"><rect width="14" height="11" rx="1" fill="#e3b021"/><path d="M1 1l6 5 6-5" stroke="#fff" stroke-width="1.4" fill="none"/></svg>
    diretoria@vantori.com
  </p>
  <p class="abs foot-line" style="top:3530px">Help<span class="sep">|</span>FAQ<span class="sep">|</span>Support<span class="sep">|</span>Sitemap<span class="sep">|</span>Terms Of Use<span class="sep">|</span>Privacy Statement</p>
  <p class="abs copy">Copyrights © 2018, Vantori. All rights reserved.</p>
</footer>

</body>
</html>
```